Church Website with Home Page and Member Sermon Library

I am in need of an updated design for our church website. This will include 4 pages (outlined below). We are a conservative, evangelical, Christian church. The site should be modern and clean, while still reflecting our conservative values. I already have a logo for our church, and I want the site to incorporate the logo, and match the logo/branding. Stock photos are allowed if needed, but I have uploaded some images of our church and would prefer those images to be used if possible. Any stock photos used should not include any people in the photos (scenery, nature, buildings, animals, etc. are fine).

The site will need 4 pages: Home, Support Us (Donate), Login, and Recording Library.

Page 1: Home
The home page should include the following sections:

- Navigation: Should include links to each section of the home page plus a "listen live" link which will take the user to a live-streaming site and a "support us" link which will take the user to a support/donate page.

- Announcements: Can be either a banner or some other design, but there needs to be some way for us to post announcements for visitors to see. I'm open for creative ideas in this section, but would like it not to take up a lot of room on the page.

- About Us: Should include address, service times (see attached document), and information about the church.

- Pastor Bio: A section that introduces our pastor and gives a short bio about our pastor. Would like this section to include a picture of our pastor. Somewhere in this section I would like to include this Bible reference: "And I will give you pastors according to mine heart, which shall feed you with knowledge and understanding. Jer 3:15 LPW"

- Articles of Faith (What We Believe): This should include several sub-sections each with a heading, body, and possibly 1 or more scripture references. I have attached a document to the brief that includes our articles of faith. Feel free to be creative with this section in how you lay these out and format them.

- Support Us: A small section that explains what kind of support someone can give and a link to a donation page. The link can say something like "Support Us" or "Donate Now".

- Contact form: A contact form that allows the visitor to send us a message. The contact form should ask for name, email, phone, and message.

- Footer: A footer that will be displayed on all pages of the site. This should include at a minimum a link to the home page (or a link to each individual section in the home page if you prefer), a link to "listen live", a link to "support us", a link to "contact us" (or you can put the contact form directly in the footer if you prefer), the address, and a "member login" link.

Page 2: Support Us
The donation page should include a form the visitor can fill out to make a donation. We will embed a third party form later. For this design, please just mock out the design with a basic form asking for name, phone, and email.

Page 3: Login
The recording library (detailed below) will require members to login with a shared numeric code before accessing the page. We need a design for a login screen. The screen should include navigation/footer just like all other pages, but the body of the login page will consist only of a form that asks the user to enter the access code and then a "login" button.

Page 4: Recording Library

The library page is a member-only page that will require a shared, numeric pass code to access. On this page, members will be able to access a filterable list of past sermons. The page by default should display most recent sermons, but should also include a search form that allows the member to filter the sermon list to find a particular sermon. The search form should allow the user to select a filter type (e.g. Speaker name, date, event, etc.) and type in a value to search. They should be able to add multiple filters and remove filters that have been added. Each sermon that is displayed in the result list should include basic information such as title, date, speaker, tags, etc. along with a download icon, and an embedded audio player where they can click a play button to stream it on-demand. Each sermon should also have clickable tags associated with it that can be used to find related sermons.
Updates

I have uploaded several images of our church. Feel free to incorporate these into your design if possible.

Target Market(s)

Church Members

Industry/Entity Type

Religion

Number of Pages Required

4 page

Font styles to use
Sans Serif

Colors

Designer to choose colors to be used in the design.

Requirements
Must have
• Must incorporate the logo (attached)
Nice to have
• Would like the design to incorporate pictures of our church (attached) instead of stock photos if possible.
Should not have
• Please avoid an overly cluttered design. Stock photos used should not include any people in the photos.

```html
<!DOCTYPE html>
<html lang="en">
<head>
<meta charset="utf-8">
<title>Grace Covenant Church</title>
<link href="https://fonts.googleapis.com/css2?family=Cinzel:wght@400;500&family=Montserrat:ital,wght@0,400;0,500;0,600;0,700;1,500&display=swap" rel="stylesheet">
<style>
:root{
  --green:#7fa765;
  --green-dark:#5d7f47;
  --green-soft:#c6d6b8;
  --green-band:#93b67d;
  --blue:#12b8dd;
  --blue-deep:#04a6d3;
  --text:#5b5b5b;
  --muted:#777;
  --grey-bg:#f3f3f2;
  --white:#fff;
}
*{box-sizing:border-box;margin:0;padding:0}
html,body{width:1200px;height:4633px;overflow:hidden}
body{position:relative;background:var(--white);font-family:"Montserrat",sans-serif;color:var(--text)}
.abs{position:absolute}
.serif{font-family:"Cinzel",serif;font-weight:400}
a{color:inherit;text-decoration:none}

/* header */
.site-header{position:absolute;left:0;top:0;width:1200px;height:88px;background:var(--white)}
.brand{position:absolute;left:118px;top:26px;display:flex;align-items:center;gap:10px}
.brand-mark{width:14px;height:14px;background:var(--green)}
.brand-name{font-family:"Cinzel",serif;font-size:20px;color:var(--green);letter-spacing:1px;line-height:1}
.main-nav{position:absolute;left:351px;top:44px;display:flex;gap:0;font-size:12px;color:var(--green-dark);letter-spacing:.3px}
.main-nav a{padding:0 20px}
.main-nav a:first-child{padding-left:0}
.main-nav .sep{color:var(--green-soft)}
.btn-head{position:absolute;top:30px;height:35px;width:123px;color:#fff;font-size:12px;display:flex;align-items:center;justify-content:center;letter-spacing:.5px}
.btn-live{left:833px;background:var(--green)}
.btn-support{left:964px;background:var(--blue)}

/* hero */
.hero-photo{position:absolute;left:0;top:88px;width:1200px;height:628px;background:linear-gradient(180deg,#f2f2f2 0%,#dcdcdc 35%,#8a8580 58%,#7b746f 72%,#c9c9c9 85%,#e8e8e8 100%)}
.welcome-frame{position:absolute;left:337px;top:178px;width:532px;height:169px;border:2px solid var(--green)}
.welcome-label{position:absolute;left:497px;top:158px;width:215px;height:36px;background:var(--green);color:#fff;font-size:22px;letter-spacing:3px;display:flex;align-items:center;justify-content:center}
.hero-title{position:absolute;left:337px;top:210px;width:532px;text-align:center;font-size:46px;line-height:56px;color:#8cad72}
.hero-title span{display:block;color:#5f6b58}
.ann-shadow{position:absolute;left:128px;top:756px;width:112px;height:82px;background:var(--green-soft)}
.ann-corner{position:absolute;left:1005px;top:640px;width:80px;height:60px;border:6px solid #fff;border-left:none;border-bottom:none}
.announcement{position:absolute;left:136px;top:648px;width:941px;height:182px;background:var(--green);color:#fff;text-align:center}
.announcement h2{font-size:32px;margin-top:42px;letter-spacing:1px}
.announcement .lead{font-size:14px;font-weight:700;margin-top:12px}
.announcement p{font-size:14px;margin-top:6px}

/* about */
.about-art{position:absolute;left:60px;top:880px}
.section-title{font-size:36px;color:var(--green);letter-spacing:1px}
.rule{height:2px;background:var(--green);position:absolute}
.about-text{position:absolute;left:633px;top:1030px;width:440px;font-size:14px;line-height:27px;color:var(--text)}
.about-text p+p{margin-top:7px}
.timing-label{position:absolute;left:637px;top:1222px;font-size:15px;font-weight:700;color:var(--green)}
.timing{position:absolute;font-size:11px;font-weight:700;color:#333}

/* pastor */
.pastor-band{position:absolute;left:0;top:1390px}
.pastor-title{position:absolute;left:137px;top:1574px;font-size:42px;color:#fff;letter-spacing:1px}
.pastor-text{position:absolute;left:141px;top:1656px;width:480px;color:#fff;font-size:14.5px;line-height:23px;font-weight:500}
.pastor-text p+p{margin-top:12px}
.quote-box{position:absolute;left:143px;top:1818px;width:475px;height:108px;border:2px solid #fff;border-radius:14px;color:#fff;padding:20px 22px 0 42px}
.quote-box q{display:block;font-style:italic;font-size:13px;line-height:20px;font-weight:500}
.quote-box cite{display:block;font-style:normal;font-size:13px;margin-top:8px;font-weight:500}
.pastor-frame{position:absolute;left:675px;top:1564px;width:373px;height:378px;border:2px solid #fff}
.pastor-photo{position:absolute;left:690px;top:1578px;width:345px;height:352px;background:linear-gradient(160deg,#b9864e 0%,#6a4b34 40%,#2a2523 70%,#3a3330 100%)}
.pastor-corner{position:absolute;left:931px;top:1826px;width:118px;height:118px;border-right:12px solid #fff;border-bottom:12px solid #fff}

/* articles */
.articles-title{position:absolute;left:0;top:2124px;width:1200px;text-align:center;font-size:38px;color:var(--green);letter-spacing:1px}
.article{position:absolute;width:445px;font-size:13.5px;line-height:26px;color:var(--text)}
.article h3{font-family:"Montserrat",sans-serif;font-weight:500;font-size:20px;letter-spacing:3px;color:#4e6840;margin-bottom:8px}
.article ol{list-style:none;font-size:12px;line-height:31px;margin-top:4px;padding-left:4px}
.article .small{font-size:12.5px;line-height:26px}
.divider{position:absolute;height:1px;background:#b7c9a9;width:445px}

/* support */
.support-bg{position:absolute;left:0;top:3060px;width:1200px;height:660px;background:var(--grey-bg)}
.support-card{position:absolute;left:433px;top:3146px;width:642px;height:426px;background:#fff;box-shadow:0 2px 14px rgba(0,0,0,.05)}
.support-photo{position:absolute;left:150px;top:3190px;width:388px;height:328px;background:linear-gradient(120deg,#c9dba1 0%,#6f9a3c 45%,#b9c9a0 80%,#e5e5e0 100%)}
.support-line-v{position:absolute;left:138px;top:3290px;width:6px;height:240px;background:var(--blue)}
.support-line-h{position:absolute;left:138px;top:3524px;width:200px;height:6px;background:var(--blue)}
.support-text{position:absolute;left:605px;top:3306px;width:410px;font-size:16px;line-height:29px;color:#444}
.btn-pill{position:absolute;background:var(--green);color:#fff;border-radius:24px;display:flex;align-items:center;justify-content:center;font-weight:700;letter-spacing:.5px}

/* contact */
.contact-band{position:absolute;left:0;top:3648px}
.contact-title{position:absolute;left:0;top:3770px;width:1200px;text-align:center;font-size:40px;color:#fff;letter-spacing:1px}
.field{position:absolute;background:#fff;font-size:13px;color:#666;padding:0 20px;display:flex;align-items:center}
.field.msg{align-items:flex-start;padding-top:18px}

/* footer */
.footer-col h4{font-family:"Montserrat",sans-serif;font-weight:500;font-size:14px;letter-spacing:2px;color:var(--green-dark);position:absolute}
.footer-links{position:absolute;font-size:13px;line-height:30px;color:#555;list-style:none}
.vline{position:absolute;width:1px;background:#ddd}
.copyright{position:absolute;left:0;top:4575px;width:1200px;height:58px;background:#f1f2ee;font-size:11px;color:#666;display:flex;align-items:center;justify-content:center}
</style>
</head>
<body>

<header class="site-header">
  <a class="brand" href="#"><span class="brand-mark"></span><span class="brand-name">Grace Covenant Church</span></a>
  <nav class="main-nav">
    <a href="#about">ABOUT US</a><span class="sep">|</span>
    <a href="#pastor">PASTOR BIO</a><span class="sep">|</span>
    <a href="#faith">ARTICLES OF FAITH</a><span class="sep">|</span>
    <a href="#contact">CONTACT</a>
  </nav>
  <a class="btn-head btn-live" href="#">LISTEN LIVE</a>
  <a class="btn-head btn-support" href="#">SUPPORT US</a>
</header>

<section class="hero">
  <div class="hero-photo" role="img" aria-label="Black and white photo of the brick church building"></div>
  <div class="welcome-frame"></div>
  <div class="welcome-label serif">WELCOME TO</div>
  <h1 class="hero-title serif">GRACE COVENANT<span>CHURCH</span></h1>
  <div class="ann-shadow"></div>
  <div class="ann-corner"></div>
  <div class="announcement">
    <h2 class="serif">ANNOUNCEMENT</h2>
    <p class="lead">LOREM IPSUM DOLOR SIT AMET CONSECTETUR ADIPISCING</p>
    <p>Ut enim ad minim veniam quis nostrud exercitation Allamco laboris nisi ut aliquip ex ea</p>
  </div>
</section>

<section id="about">
  <svg class="about-art" width="560" height="510" viewBox="0 0 560 510">
    <defs>
      <linearGradient id="blueFrame" x1="0" y1="0" x2="1" y2="1">
        <stop offset="0" stop-color="#1cc6e8"/><stop offset="1" stop-color="#0aa7d4"/>
      </linearGradient>
      <linearGradient id="churchPhoto" x1="0" y1="0" x2="0" y2="1">
        <stop offset="0" stop-color="#e9eaec"/><stop offset=".45" stop-color="#d5d7da"/>
        <stop offset=".5" stop-color="#9a6a52"/><stop offset=".72" stop-color="#8a5d47"/>
        <stop offset=".78" stop-color="#b9b9b6"/><stop offset="1" stop-color="#cfcfcc"/>
      </linearGradient>
      <clipPath id="diamondClip"><polygon points="278,10 522,254 278,498 34,254"/></clipPath>
    </defs>
    <polygon points="8,254 150,112 150,126 22,254 150,382 150,396" fill="url(#blueFrame)"/>
    <polygon points="140,80 8,212 8,296 170,458 186,442 40,254 160,100" fill="url(#blueFrame)" opacity="0"/>
    <polygon points="8,254 165,97 178,110 34,254 178,398 165,411" fill="url(#blueFrame)"/>
    <g clip-path="url(#diamondClip)">
      <rect x="34" y="10" width="488" height="488" fill="url(#churchPhoto)" role="img" aria-label="Photo of the brick church exterior"/>
    </g>
    <polyline points="300,20 540,254 300,488" fill="none" stroke="#7fa765" stroke-width="1.5"/>
    <polyline points="316,40 532,254 316,468" fill="none" stroke="#7fa765" stroke-width="1.5"/>
  </svg>
  <h2 class="abs section-title serif" style="left:633px;top:950px">ABOUT OUR CHURCH</h2>
  <div class="rule" style="left:633px;top:1006px;width:70px"></div>
  <div class="about-text">
    <p>Lorem ipsum dolor sit amet, consectetur adipiscing elit, sed do eiusmod tempor incididunt ut labore et dolore magna aliqua. Ut enim ad minim veniam, quis nostrud exercitation</p>
    <p>Allamco laboris nisi ut aliquip ex ea commodo consequat. Duis aute irure dolor in reprehenderit in voluptate velit esse cillum dolore eu fugiat nulla pariatur.</p>
  </div>
  <div class="timing-label">SERVICE TIMING:</div>
  <div class="timing" style="left:637px;top:1260px">Wednesday Night Service: 7:30 PM</div>
  <div class="timing" style="left:879px;top:1260px">Sunday Morning Service: 11:00 AM</div>
  <div class="timing" style="left:637px;top:1291px">Sunday School: 10:00 AM</div>
  <div class="timing" style="left:879px;top:1291px">Sunday Night Service: 5:30 PM</div>
</section>

<section id="pastor">
  <svg class="pastor-band" width="1200" height="654" viewBox="0 0 1200 654" role="img" aria-label="Blue tinted photo of the church building">
    <defs>
      <linearGradient id="blueBand" x1="0" y1="0" x2="0" y2="1">
        <stop offset="0" stop-color="#0bbadf"/><stop offset=".6" stop-color="#22b8dd"/><stop offset="1" stop-color="#3fa9cc"/>
      </linearGradient>
    </defs>
    <polygon points="0,0 603,96 1200,0 1200,654 0,654" fill="url(#blueBand)"/>
    <polygon points="0,0 603,96 1200,0 1200,8 603,108 0,8" fill="#9fe3f3" opacity=".7"/>
  </svg>
  <h2 class="pastor-title serif">OUR PASTOR</h2>
  <div class="rule" style="left:141px;top:1634px;width:96px;background:#fff"></div>
  <div class="pastor-text">
    <p>Lorem ipsum dolor sit amet, consectetur adipiscing elit, sed do eiusmod tempor incididunt ut labore et dolore magna aliqua. Ut enim ad minim veniam, quis nostrud exercitation</p>
    <p>Allamco laboris nisi ut aliquip ex ea commodo consequat. Duis aute irure dolor in reprehenderit in voluptate velit esse</p>
  </div>
  <blockquote class="quote-box">
    <q>“And I will give you pastors according to mine heart, which shall feed you with knowledge and understanding”</q>
    <cite>Jer 3:15 LPW</cite>
  </blockquote>
  <div class="pastor-frame"></div>
  <div class="pastor-photo" role="img" aria-label="Portrait of the pastor holding an open Bible"></div>
  <div class="pastor-corner"></div>
</section>

<section id="faith">
  <h2 class="articles-title serif">ARTICLES OF FAITH</h2>
  <div class="rule" style="left:555px;top:2182px;width:90px"></div>

  <div class="article" style="left:148px;top:2236px">
    <h3>THE GOD HEAD.</h3>
    <p>We believe in the God head bodily, known as the Divine Trinity. This body consist of God the father, Jesus Christ, his only begotten son and the redeemer of the world, and of the Holy Ghost, The third person of the Divine Trinity.</p>
  </div>
  <div class="article" style="left:645px;top:2236px">
    <h3>BAPTISM OF THE HOLY GHOST</h3>
    <p>We believe in the baptism of the Holy Ghost as it is taught in the Bible and promised by our Lord Jesus Christ, with speaking in tongues as the Spirit gives utterance as the initial evidence. Acts 2:4 we believe that the gift of the Holy Ghost is for all believers as the Lord promised. Acts 2:17-1</p>
  </div>
  <div class="divider" style="left:148px;top:2426px"></div>
  <div class="divider" style="left:640px;top:2426px"></div>

  <div class="article" style="left:148px;top:2456px">
    <h3>FULL SALVATION</h3>
    <p class="small">We believe that Salvation is received only when a person comes to the realization that he or she is lost and separated from God and becomes full of godly sorrow, confessing their sins and true repentance, believing in the shed blood of the Lord Jesus Christ as the only sacrifice for sins. Through the blood of Christ we have:</p>
    <ol>
      <li>(1) remission of sins, Matthew 26:28 Heb 9:22</li>
      <li>(2) Sanctification. Hebrews 13:12</li>
      <li>(3) redemption. Revelations 5:9</li>
      <li>(4) cleansing. 1 John 1:7 Rev. 1:5</li>
      <li>(5). Justification. Romans 5:9</li>
    </ol>
  </div>
  <div class="article" style="left:645px;top:2456px">
    <h3>DIVINE HEALING</h3>
    <p>We believe Divine Healing to be included in the atonement of Jesus Christ our Lord, And believe that it is still for us today. 1 Peter 2:24 Luke 9:1-2 Mark 16-18 James 5:15</p>
  </div>
  <div class="divider" style="left:640px;top:2608px"></div>
  <div class="article" style="left:645px;top:2648px">
    <h3>SECOND COMING OF CHRIST</h3>
    <p>We believe in the second coming of Jesus Christ. Matthew 24:44 Luke 12:40</p>
  </div>
  <div class="divider" style="left:148px;top:2796px"></div>
  <div class="divider" style="left:640px;top:2796px"></div>

  <div class="article" style="left:150px;top:2832px">
    <h3>SANCTIFICATION</h3>
    <p>“Sanctify them through thy truth thy word is truth St John 17:17. For this is the will of God even your sanctification”</p>
    <p style="margin-top:6px">We believe in a set apart life, separate from the world to Christ 2 Cor 6:17-18</p>
  </div>
  <div class="article" style="left:645px;top:2832px">
    <h3>ETERNITY</h3>
    <p>We believe in Literal Eternity. Eternal Life for the believer and eternal death for those without Christ. Revelations 21:1-27</p>
  </div>
</section>

<section id="support">
  <div class="support-bg"></div>
  <div class="support-card"></div>
  <div class="support-line-v"></div>
  <div class="support-line-h"></div>
  <div class="support-photo" role="img" aria-label="Coins dropped into a glass donation jar"></div>
  <h2 class="abs section-title serif" style="left:605px;top:3240px">SUPPORT US</h2>
  <div class="rule" style="left:605px;top:3290px;width:62px"></div>
  <p class="support-text">Lorem ipsum dolor sit amet, consectetur adipiscing elit, sed do eiusmod tempor incididunt ut labore et dolore magna aliqua. Ut enim ad minim veniam, quis nostrud exercitation</p>
  <a class="btn-pill" href="#" style="left:602px;top:3440px;width:186px;height:44px;font-size:13px">DONATE NOW</a>
</section>

<section id="contact">
  <svg class="contact-band" width="1200" height="615" viewBox="0 0 1200 615" role="img" aria-label="Green tinted photo of the church building">
    <defs>
      <linearGradient id="greenBand" x1="0" y1="0" x2="0" y2="1">
        <stop offset="0" stop-color="#8db47a"/><stop offset=".5" stop-color="#9bbc88"/><stop offset="1" stop-color="#8eb27a"/>
      </linearGradient>
    </defs>
    <polygon points="0,72 600,4 1200,70 1200,615 0,615" fill="url(#greenBand)"/>
    <polyline points="0,72 600,4 1200,70" fill="none" stroke="#6f9858" stroke-width="4"/>
  </svg>
  <h2 class="contact-title serif">CONTACT US</h2>
  <div class="rule" style="left:555px;top:3830px;width:90px;background:#fff"></div>
  <div class="field" style="left:216px;top:3866px;width:389px;height:48px">First Name</div>
  <div class="field" style="left:616px;top:3866px;width:389px;height:48px">Last Name</div>
  <div class="field" style="left:216px;top:3932px;width:389px;height:48px">Email address</div>
  <div class="field" style="left:616px;top:3932px;width:389px;height:48px">Phone</div>
  <div class="field msg" style="left:216px;top:3992px;width:789px;height:98px">Message</div>
  <a class="btn-pill" href="#" style="left:516px;top:4126px;width:194px;height:44px;font-size:14px;background:var(--blue);font-weight:500">SEND MESSAGE</a>
</section>

<footer class="site-footer">
  <a class="brand" href="#" style="top:4362px;left:148px"><span class="brand-mark"></span><span class="brand-name" style="font-size:18px">Grace Covenant Church</span></a>
  <div class="vline" style="left:407px;top:4263px;height:312px"></div>
  <div class="vline" style="left:607px;top:4263px;height:312px"></div>
  <div class="vline" style="left:862px;top:4263px;height:312px"></div>

  <div class="footer-col">
    <h4 style="left:432px;top:4322px">NAVIGATION</h4>
    <div class="rule" style="left:432px;top:4322px;width:2px;height:16px;background:var(--blue);display:none"></div>
    <ul class="footer-links" style="left:436px;top:4353px">
      <li>About Us</li><li>Pastor Bio</li><li>Article of Faith</li><li>Listen Live</li><li>Contact Us</li>
    </ul>
  </div>
  <div class="footer-col">
    <h4 style="left:628px;top:4322px">DONATION</h4>
    <p class="abs" style="left:631px;top:4357px;width:210px;font-size:12px;line-height:18px;color:#666">Lorem ipsum dolor sit amet, consectetur adipiscing elit, sed do eiusmod tempor inci</p>
    <a class="btn-pill" href="#" style="left:628px;top:4436px;width:132px;height:30px;font-size:10px;font-weight:500">DONATE NOW</a>
  </div>
  <div class="footer-col">
    <h4 style="left:892px;top:4324px">CONTACT US</h4>
    <svg class="abs" style="left:888px;top:4362px" width="30" height="30" viewBox="0 0 30 30" aria-hidden="true">
      <circle cx="15" cy="15" r="15" fill="#7fa765"/>
      <path d="M15 7a5.5 5.5 0 0 0-5.5 5.5c0 4 5.5 10 5.5 10s5.5-6 5.5-10A5.5 5.5 0 0 0 15 7z" fill="#fff"/>
      <circle cx="15" cy="12.5" r="2" fill="#7fa765"/>
    </svg>
    <p class="abs" style="left:932px;top:4358px;width:150px;font-size:11.5px;line-height:17px;color:#444">88 Meadow Lane, Suite 210, Fairview,<br>OH 45102 USA</p>
    <a class="btn-pill" href="#" style="left:887px;top:4430px;width:134px;height:30px;font-size:10px;font-weight:500;background:var(--blue)">MEMBER LOGIN</a>
  </div>
  <div class="copyright">© 2023 Grace Covenant Church. All Rights Reserved</div>
</footer>

</body>
</html>
```